Brightwater Care Partners, LLC Business Card update!

would like a classier business card. Our cards currently just have our logo and contact information. Need better use of color and creativity
Logo attached.

Target Market(s)

Potential clients, contacts, existing clients. We are a consulting company

Industry/Entity Type

Business

Contact Information for Business Card

We like our colors but just have a boring card with our logo and a white background. I want something that stands out.

Colors
ec1f27
757575

Requirements
Must have
• Color to stay consistent. Logo provided
Nice to have
• Just better use of color/ design

```html
<!DOCTYPE html>
<html lang="en">
<head>
<meta charset="utf-8">
<title>Brightwater Care Partners – Business Card</title>
<link rel="stylesheet" href="https://fonts.googleapis.com/css2?family=Lato:wght@400;700&display=swap">
<style>
  :root {
    --brand-red: #ec1f27;
    --brand-red-deep: #c8181f;
    --band-dark: #2a2627;
    --ink-white: #ffffff;
    --ink-soft: #f2f2f2;
    --stage: #1c1c1c;
  }
  * { margin: 0; padding: 0; box-sizing: border-box; }
  html, body {
    width: 1200px;
    height: 900px;
    overflow: hidden;
    background: var(--stage);
    font-family: "Lato", Arial, sans-serif;
  }
  .stage {
    width: 1200px;
    height: 900px;
    display: flex;
    align-items: center;
    justify-content: center;
  }
  .business-card {
    position: relative;
    width: 910px;
    height: 520px;
    background: radial-gradient(ellipse at 50% 40%, var(--brand-red) 55%, var(--brand-red-deep) 100%);
    color: var(--ink-white);
    overflow: hidden;
  }
  .brand {
    position: absolute;
    top: 70px;
    left: 0;
    right: 0;
    display: flex;
    align-items: center;
    justify-content: center;
    gap: 24px;
  }
  .brand-dot {
    width: 64px;
    height: 64px;
    border-radius: 50%;
    background: var(--ink-white);
    flex: none;
  }
  .brand-name {
    font-size: 56px;
    font-weight: 400;
    letter-spacing: 0.5px;
    line-height: 1;
    color: var(--ink-white);
  }
  .identity-band {
    position: absolute;
    top: 238px;
    left: 0;
    right: 0;
    height: 128px;
    background: var(--band-dark);
    display: flex;
    flex-direction: column;
    align-items: center;
    padding-top: 26px;
  }
  .owner-name {
    font-size: 40px;
    font-weight: 400;
    letter-spacing: 1px;
    color: var(--ink-soft);
    line-height: 1.1;
  }
  .owner-title {
    font-size: 24px;
    font-weight: 400;
    letter-spacing: 0.5px;
    color: var(--ink-soft);
    margin-top: 4px;
  }
  .contact-list {
    position: absolute;
    top: 392px;
    left: 0;
    right: 0;
    list-style: none;
    display: flex;
    flex-direction: column;
    align-items: center;
    gap: 6px;
  }
  .contact-item {
    display: flex;
    align-items: center;
    gap: 12px;
    font-size: 25px;
    letter-spacing: 0.5px;
  }
  .contact-icon {
    width: 18px;
    height: 18px;
    fill: var(--ink-white);
    flex: none;
  }
</style>
</head>
<body>
  <main class="stage">
    <article class="business-card">
      <header class="brand">
        <span class="brand-dot" aria-hidden="true"></span>
        <span class="brand-name">Brightwater Care Partners</span>
      </header>

      <section class="identity-band">
        <p class="owner-name">Owner Name</p>
        <p class="owner-title">Designation</p>
      </section>

      <ul class="contact-list">
        <li class="contact-item">
          <svg class="contact-icon" viewBox="0 0 24 24" aria-hidden="true">
            <path d="M3 8c0-2 4-4 9-4s9 2 9 4v2h-5V8c-1-.6-2.5-1-4-1s-3 .4-4 1v2H3z"/>
            <path d="M6 12h12l2 8H4z"/>
          </svg>
          <span>(555) 010-2468</span>
        </li>
        <li class="contact-item">
          <svg class="contact-icon" viewBox="0 0 24 24" aria-hidden="true">
            <path d="M2 5h20v14H2z M3.5 6.5 12 13l8.5-6.5" fill="var(--ink-white)"/>
            <path d="M3 6l9 7 9-7" fill="none" stroke="var(--brand-red)" stroke-width="1.6"/>
          </svg>
          <span>info@brightwatercare.com</span>
        </li>
      </ul>
    </article>
  </main>
</body>
</html>
```